VL - menu design

Hi,

We require elegant menu design for upscale restaurant. Please find attached the logo and the menu items for your reference.

for inspiration, this is a good website: -
http://www.plateworthy-sample.net/dishcraft/about.php

We are very much open for Menu Size suggestions.

unfortunately the place is going under renovation, we don't have updated images to it. the closest look and feel to our place is http://vazelo-example.com ..

we are also open for creative options on the shape, the styles, etc. as long as it represents the fine dine feel ...

Thanks ...

Dear All,

We wouldlike to extend our apology for not being able to provide feedbacks on everysingle design. We were extremely busy and we have multiple contests opensimultaneously which makes the process even harder.

However,we would like to thank you all for the efforts you have put into designingour menu. It is very much appreciated …

We wishyou all success in your design ventures and we are quite positive that we willbe working with many of you on many projects in the soon future. 

Thanks & Regards,

DQI Team...

 

 

 

Industry/Entity Type

Restaurant

Requirements
Must have
• Please ensure that there are 'some' images in the menu ... this is very important.
Should not have
• IMPORTANT: -

1. Please DO NOT insert any currency sign to the menu
2. Please keep the prices of the menu at the end of the menu items descriptions NOT beside the menu item names. The font of the price should be similar to the menu item description and please DO NOT bold the numbers. the prices should be subtle.

Thank you ...

```html
<!DOCTYPE html>
<html lang="en">
<head>
<meta charset="utf-8">
<title>Lantern Row Café – Menu Set</title>
<link href="https://fonts.googleapis.com/css2?family=Exo+2:wght@300;400&family=Playfair+Display:ital,wght@1,700&family=Crimson+Text:ital@1&display=swap" rel="stylesheet">
<style>
:root{
  --ink:#231f20;
  --tan:#a88a68;
  --brown:#97734e;
  --text:#3b3836;
  --rule:#cfcac4;
  --paper:#ffffff;
  --sketch:#d9cbb8;
}
*{box-sizing:border-box;margin:0;padding:0}
html,body{width:1200px;height:1000px;overflow:hidden;background:var(--paper)}
.canvas{position:relative;width:1200px;height:1000px}
.sheet{position:absolute;background:var(--paper);box-shadow:0 1px 5px rgba(0,0,0,.28);overflow:hidden}
.brand{position:absolute;background:var(--ink);display:flex;flex-direction:column;align-items:center;justify-content:center;color:#fff;font-family:'Exo 2',sans-serif;font-weight:300;text-align:center;line-height:1.1}
.brand .name{font-size:13px;letter-spacing:2px;white-space:nowrap}
.brand .sub{font-size:6px;letter-spacing:3px}
.sketch{position:absolute;border-radius:40%;background:radial-gradient(ellipse at center,var(--sketch) 0%,#ece4d8 60%,rgba(255,255,255,0) 75%)}
.head{font-family:'Exo 2',sans-serif;font-weight:300;color:#4a4542;text-transform:uppercase;letter-spacing:.5px;border-top:1px solid var(--rule);border-bottom:1px solid var(--rule);padding:2px 0;text-align:center;font-size:12px}
.col{position:absolute;text-align:center;color:var(--text)}
.col.left{text-align:left}
.nm{font-family:'Playfair Display',serif;font-style:italic;font-weight:700;color:var(--brown);font-size:6.4px;margin-top:5px}
.ds{font-family:'Crimson Text',serif;font-style:italic;font-size:4.6px;line-height:1.3}
.ln{font-family:'Playfair Display',serif;font-style:italic;font-weight:700;font-size:5.2px;line-height:1.55;color:var(--text)}
.ln span{font-family:'Crimson Text',serif;font-weight:400}
.sublabel{font-family:'Playfair Display',serif;font-weight:700;font-size:6px;color:var(--brown);text-transform:uppercase;margin-top:4px}
.vrule{position:absolute;width:1px;background:var(--rule)}
.frame{position:absolute;border:1px solid var(--rule)}
.frame::before,.frame::after{content:"";position:absolute;width:8px;height:8px;border-color:#8c8780;border-style:solid}
.frame::before{top:-3px;left:-3px;border-width:1px 0 0 1px}
.frame::after{bottom:-3px;right:-3px;border-width:0 1px 1px 0}

.cover{position:absolute;left:131px;top:33px;width:436px;height:424px;background:var(--ink);box-shadow:0 1px 5px rgba(0,0,0,.35)}
.cover .spine{position:absolute;left:0;top:0;width:14px;height:100%;background:var(--tan)}
.cover .corner{position:absolute;width:6px;height:14px;background:var(--tan)}
.cover .brand{left:120px;top:180px;width:240px;height:70px;background:none}
.cover .brand .name{font-size:22px;letter-spacing:4px}
.cover .brand .sub{font-size:8px;letter-spacing:5px;color:var(--tan)}
</style>
</head>
<body>
<div class="canvas">

  <div class="cover">
    <div class="spine"></div>
    <div class="corner" style="right:0;top:0"></div>
    <div class="corner" style="right:0;bottom:0"></div>
    <div class="brand"><div class="name">LANTERN ROW</div><div class="sub">CAFÉ</div></div>
  </div>

  <div class="sheet" style="left:626px;top:35px;width:422px;height:422px">
    <div class="brand" style="left:0;top:0;width:134px;height:78px"><div class="name">LANTERN ROW</div><div class="sub">CAFÉ</div></div>
    <div class="sketch" role="img" aria-label="Sketch of a stacked club sandwich" style="left:218px;top:42px;width:90px;height:62px"></div>

    <div class="col" style="left:26px;top:128px;width:124px">
      <div class="head">The Breakfast</div>
      <div class="nm">Butter Croissant</div><div class="ds">Served plain with a selection of jams, a vanilla custard cream, a chocolate cream and butter curls. 36</div>
      <div class="nm">Cheese Croissant</div><div class="ds">Crumbly freshly baked with cheese filling. 29</div>
      <div class="nm">Daily Fresh Eggs</div><div class="ds">A choice of poached, scrambled, pan fried, omelet, all served with toasted bread, mushrooms, roasted tomatoes and chicken sausages. 59</div>
      <div class="nm">Healthy Time</div><div class="ds">One choice of hot beverage from our cafe served with fruit salad, natural yoghurt, whole wheat bread vegetable sandwiches and sugar free biscuits selection. 49</div>
      <div class="nm">Energy Time</div><div class="ds">One choice of hot beverage from our cafe served with finger chocolate muffins, poached egg with toasted bread and crispy beef bacon, crepe roll with goat cheese and honey and finger chocolate cream with salted cookies. 59</div>
      <div class="nm">Lantern Row Time</div><div class="ds">One choice of hot beverage from our cafe served with our selection of scones, smoked salmon and avocado sandwich, roasted sausages sandwich, grilled vegetables sandwich, selection of our best biscuits. 59</div>
      <div class="nm">The Arabic Breakfast</div><div class="ds">Choice of zaatar manakish and cheese manakish, served with one choice of hot beverage from our cafe and fresh orange juice. 59</div>
    </div>

    <div class="col" style="left:152px;top:110px;width:244px">
      <div class="head">The Sandwiches</div>
      <div class="ds" style="margin-top:5px"><b class="ln">Grilled Vegetables Sandwich</b> with fresh goat cheese and chives served with our homemade spicy garlic mayo. 59</div>
      <div class="ds" style="margin-top:4px"><b class="ln">Butterfish burger</b> with fresh tomato, beef bacon, grilled vegetables and béarnaise sauce.</div>
      <div class="ds" style="margin-top:4px"><b class="ln">Tataki Tuna sandwich</b> with red onion slices, steamed endives and black olives and cashew paté. 79</div>
      <div class="ds" style="margin-top:4px"><b class="ln">Beef sirloin steak sandwich</b> with grain mustard, parmesan cheese and fresh Nashi pears. 79</div>
      <div class="ds" style="margin-top:4px"><b class="ln">The Traditional Club sandwich</b> served with French fries and vegetable chips. 69</div>
      <div class="ds" style="margin-top:4px"><b class="ln">Chicken sandwich</b> with parmesan cheese slices, sundried tomatoes and mint flavored mayo. 69</div>
    </div>

    <div class="col" style="left:152px;top:210px;width:176px">
      <div class="head">Salads</div>
      <div class="nm">Vegetarian Salad</div><div class="ds">Fresh green leaves, Italian cherry tomatoes, carrots, cucumber, green apple and toasted pine nuts with our special grain mustard dressing. 59</div>
      <div class="nm">Sweet Gorgonzola Cheese Salad</div><div class="ds">Fresh green leaves, gorgonzola cheese, fresh pears, walnuts, garlic bread croutons, green celery with smoked honey dressing. 59</div>
      <div class="nm">Beef Sirloin Salad</div><div class="ds">Fresh green leaves, beef sirloin julienne, caramelized apples, parmesan cheese, toasted almonds, sundried tomatoes and light pesto sauce. 79</div>
      <div class="nm">Tandoori Chicken Salad</div><div class="ds">Fresh green leaves, tandoori chicken breast, fresh mango, fresh goat cheese, crispy chicken skin and jasmine rice sauce. 69</div>
      <div class="nm">Seafood Salad</div><div class="ds">Fresh green leaves, fresh steamed seafood, black olives, celery, garlic bread croutons, avocado and grapefruit dressing. 89</div>
      <div class="nm">Fresh Tuna Salad</div><div class="ds">Fresh green leaves, low temperature cooked tuna, taggiasca olives, red onions, roasted peppers, soy marinated tofu and lemon dressing. 89</div>
    </div>
    <div class="vrule" style="left:329px;top:226px;height:180px"></div>
    <div class="col" style="left:332px;top:226px;width:66px">
      <div class="head">Soup</div>
      <div class="nm">Bouillabaisse</div><div class="ds">Traditional French seafood soup, with saffron and estragon. 119</div>
      <div class="nm">Barley soup</div><div class="ds">With fresh vegetables, tomato smoothie and a hint of garlic oil. 49</div>
      <div class="nm">Beef chili</div><div class="ds">Served with Arabic bread, fresh guacamole and spicy black beans. 49</div>
    </div>
    <div class="sketch" role="img" aria-label="Sketch of a soup bowl with vegetables" style="left:336px;top:358px;width:52px;height:40px"></div>
  </div>

  <div class="sheet" style="left:42px;top:508px;width:436px;height:430px;transform:rotate(-3deg);transform-origin:0 0">
    <div class="brand" style="left:0;top:0;width:142px;height:86px"><div class="name">LANTERN ROW</div><div class="sub">CAFÉ</div></div>
    <div class="sketch" role="img" aria-label="Sketch of a roast chicken" style="left:236px;top:20px;width:90px;height:52px"></div>

    <div class="col" style="left:160px;top:78px;width:262px">
      <div class="head">First Courses</div>
      <div class="ds" style="margin-top:4px"><b class="ln">Tagliatelle served on a whole Lobster</b> with fresh asparagus, cherry tomato and crispy beef bacon. 249</div>
      <div class="ds" style="margin-top:3px"><b class="ln">Whole wheat Maltagliati</b> with porcini mushrooms and brown butter. 89</div>
      <div class="ds" style="margin-top:3px"><b class="ln">Penne pasta with fresh broccoli</b>, taleggio cheese cream, toasted almonds. 79</div>
      <div class="ds" style="margin-top:3px"><b class="ln">Spaghetti</b> with a smooth and creamy sauce and juicy chicken. 79</div>
      <div class="ds" style="margin-top:3px"><b class="ln">Fettuccine with fresh salmon</b>, saffron and toasted pine nuts. 89</div>
      <div class="ds" style="margin-top:3px"><b class="ln">Seaweed tagliatelle</b> with king scallops and poached egg. 99</div>
      <div class="ds" style="margin-top:3px"><b class="ln">Risotto with Prawns</b>, green peas and lemon reduction. 99</div>
      <div class="ds" style="margin-top:3px"><b class="ln">Risotto "Primavera"</b> with fresh seasonal vegetables served on a stone. 79</div>
      <div class="ds" style="margin-top:3px"><b class="ln">Risotto with porcini mushrooms</b> and parmesan. 89</div>
    </div>

    <div class="col" style="left:28px;top:140px;width:136px">
      <div class="head">Appetizers</div>
      <div class="ds" style="margin-top:5px"><b class="ln">Fresh tomato and mozzarella</b> terrine with basil sauce, black olives and fresh capers. 69</div>
      <div class="ds" style="margin-top:4px"><b class="ln">Fresh salmon sashimi</b> seared in olive oil with spring and red onions, orange zest and fresh sweet chili. 79</div>
      <div class="ds" style="margin-top:4px"><b class="ln">Duck Foie Gras</b> terrine with toasted pan brioche and red onion jam spheres. 124</div>
      <div class="ds" style="margin-top:4px"><b class="ln">Selection of vegetables</b> stuffed with fresh spinach, goat cheese and fresh mint on a garlic tomato coulis. 93</div>
      <div class="ds" style="margin-top:4px"><b class="ln">Grilled Octopus</b> with bell peppers, roasted tofu, lemon zest and sweet n' sour soy drops. 99</div>
      <div class="ds" style="margin-top:4px"><b class="ln">Sea Scallops "au gratin"</b> with garlic chips, walnut cream and truffle oil. 176</div>
      <div class="ds" style="margin-top:4px"><b class="ln">Irish Beef "Carpaccio"</b> on a Bagna Cauda sauce and truffle slices, with toasted pine nuts and seasonal fresh salad. 79</div>
      <div class="ds" style="margin-top:4px"><b class="ln">Prawns</b> with white chocolate sauce, thyme creamy, fresh celery on a Vitelotte potato cream. 89</div>
    </div>
    <div class="sketch" role="img" aria-label="Sketch of a plate of dumplings" style="left:62px;top:372px;width:66px;height:40px"></div>

    <div class="vrule" style="left:166px;top:200px;height:200px"></div>
    <div class="col" style="left:170px;top:200px;width:132px">
      <div class="head">Main Courses</div>
      <div class="ds" style="margin-top:5px"><b class="ln">Grilled beef tenderloin</b> with balsamic sauce, mashed potatoes and grilled pumpkin. 149</div>
      <div class="ds" style="margin-top:4px"><b class="ln">Chicken supreme</b> stuffed with fontina cheese, spinach and black olives in a crispy panko crust served on aubergine "Caponata". 139</div>
      <div class="ds" style="margin-top:4px"><b class="ln">Grilled fresh Salmon</b> dusted in herbs with seasonal sautéed vegetables with sesame and light soy sauce. 14</div>
      <div class="ds" style="margin-top:4px"><b class="ln">Sea Bass</b> crumble with smashed potato and zucchini ratatouille. 159</div>
      <div class="ds" style="margin-top:4px"><b class="ln">The Paella</b>, traditional Spanish seafood and chicken dish, served with saffron rice and green peas. 229</div>
      <div class="ds" style="margin-top:4px"><b class="ln">Stuffed calamari</b> with breadcrumbs, black olives, green peas served on a semolina cream and fresh tomato sauce.</div>
    </div>
    <div class="vrule" style="left:305px;top:200px;height:200px"></div>
    <div class="col" style="left:308px;top:200px;width:120px">
      <div class="head">The Roasts</div>
      <div class="ds" style="margin-top:5px"><b class="ln">Spring Lamb</b> marinated in fresh herbs with roasted potatoes and rosemary jus. 169</div>
      <div class="ds" style="margin-top:4px">Roasted in banana leaves with potatoes "Fondante" and red onion ragout. 149</div>
      <div class="ds" style="margin-top:4px"><b class="ln">Baby Chicken</b> stuffed with herbs on seasoned breadcrumbs. 129</div>
    </div>
  </div>

  <div class="sheet" style="left:398px;top:497px;width:420px;height:432px;transform:rotate(2deg);transform-origin:0 0">
    <div class="brand" style="left:0;top:0;width:138px;height:76px"><div class="name">LANTERN ROW</div><div class="sub">CAFÉ</div></div>
    <div class="sketch" role="img" aria-label="Sketch of a whole pizza" style="left:200px;top:16px;width:120px;height:70px"></div>

    <div class="frame" style="left:36px;top:128px;width:166px;height:160px"></div>
    <div class="col" style="left:44px;top:134px;width:150px">
      <div class="head" style="border:none">Our Specialties</div>
      <div class="nm">Astice e Tartufo Pizza</div><div class="ds">Fresh cherry tomatoes, lobster medallions, asparagus tips, mozzarella, fresh truffle. 459</div>
      <div class="nm">Beef Tenderloin "ALLA Rossini"</div><div class="ds">With foie gras and white truffle, gratin potatoes and black peppered vegetables. 489</div>
      <div class="nm">Traditional Italian T-bone steak "ALLA Fiorentina"</div><div class="ds">(minimum 1 kg) with grilled vegetables, porcini mushrooms, béarnaise sauce and baked potatoes. 389</div>
      <div class="nm">Fettuccine with fresh white Truffle</div><div class="ds">on a leek and chives sauce. 299</div>
    </div>

    <div class="frame" style="left:36px;top:300px;width:166px;height:112px"></div>
    <div class="col" style="left:44px;top:304px;width:150px">
      <div class="head" style="border:none">Desserts</div>
      <div class="nm">Amaretto Tiramisù. 40</div>
      <div class="nm">Meringata</div><div class="ds">Traditional Italian meringue with vanilla cream, fresh strawberry and dark chocolate curls. 60</div>
      <div class="nm">Fresh Fruit Tart</div>
      <div class="nm">A slice of cake</div>
      <div class="nm">Choice of our home made cakes</div>
    </div>
    <div class="sketch" role="img" aria-label="Sketch of a pair of cherries" style="left:40px;top:318px;width:28px;height:26px"></div>

    <div class="col" style="left:214px;top:112px;width:180px">
      <div class="head">The Pizza</div>
      <div class="nm">Margherita</div><div class="ds">Fresh cherry tomatoes, buffalo mozzarella, fresh basil. 49</div>
      <div class="nm">Marinara</div><div class="ds">Tomato, salted anchovies, fresh garlic, capers, oregano. 39</div>
      <div class="nm">Capricciosa</div><div class="ds">Tomato, buffalo mozzarella, mushrooms, black olives, artichokes, turkey ham. 59</div>
      <div class="nm">Tonno e cipolle</div><div class="ds">Tomato, olive oil tuna, red onions, black olives. 79</div>
      <div class="nm">Frutti di mare</div><div class="ds">Fresh cherry tomatoes, mussels, prawns, calamari, mozzarella, olives. 99</div>
      <div class="nm">Prosciutto e funghi</div><div class="ds">Tomato, turkey ham, porcini mushrooms, parmesan slices. 69</div>
      <div class="nm">Calzone</div><div class="ds">Tomato, ricotta cheese, mozzarella, turkey ham, mushrooms, chicken sausages. 79</div>
      <div class="nm">Quattro formaggi</div><div class="ds">Mozzarella, gorgonzola cheese, fontina cheese, parmesan slices. 69</div>
      <div class="nm">Vegetariana</div><div class="ds">Fresh cherry tomatoes, mozzarella, zucchini, aubergine, bell peppers, escarole, red onions. 69</div>
      <div class="nm">Lantern Row</div><div class="ds">Fresh cherry tomatoes, buffalo mozzarella, asparagus tips, "Bufalino" style beef strips, fresh porcini mushrooms, truffle oil. 159</div>
      <div class="nm">Camel</div><div class="ds">Special pizza with camel meat flavored in Emirates style topped with mozzarella cheese. 89</div>
    </div>
  </div>

  <div class="sheet" style="left:752px;top:492px;width:440px;height:430px">
    <div class="brand" style="left:22px;top:0;width:136px;height:76px"><div class="name">LANTERN ROW</div><div class="sub">CAFÉ</div></div>

    <div class="col left" style="left:24px;top:92px;width:150px">
      <div class="head">Coffee</div>
      <div style="display:flex;gap:8px;margin-top:4px">
        <div class="ln" style="width:58px">Coffee Americano. <span>30</span><br>Cappuccino. <span>35</span><br>Latte Macchiato. <span>35</span></div>
        <div class="ln">Espresso. <span>24</span><br>Espresso Doppio. <span>35</span><br>Espresso Decaffeinato. <span>23</span><br>Mocka Roma. <span>39</span><br>Cappuccino Viennese. <span>39</span><br>Hot Chocolate. <span>35</span><br>Turkish coffee. <span>25</span></div>
      </div>
    </div>
    <div class="sketch" role="img" aria-label="Sketch of roasted coffee beans" style="left:24px;top:150px;width:68px;height:40px"></div>
    <div class="vrule" style="left:177px;top:92px;height:96px"></div>
    <div class="col left" style="left:182px;top:92px;width:70px">
      <div class="head">Hot Tea</div>
      <div class="ln" style="margin-top:4px">English breakfast. <span>35</span><br>Pure Green tea. <span>35</span><br>Earl Gray. <span>35</span><br>Jasmine. <span>35</span><br>Mint. <span>35</span><br>Peppermint. <span>35</span><br>Herbal. <span>35</span></div>
    </div>

    <div class="col" style="left:24px;top:192px;width:228px">
      <div class="head">Cold Beverages</div>
    </div>
    <div class="col left" style="left:24px;top:218px;width:70px">
      <div class="sublabel" style="margin-top:0">Ice Teas</div>
      <div class="ln">Peach Ice Tea. <span>30</span><br>Lemon Ice Tea. <span>30</span><br>Mint Ice Tea. <span>30</span><br>Water / Soda<br>Cola. <span>20</span><br>Diet Cola. <span>20</span><br>Lemon Soda. <span>20</span><br>Diet Lemon Soda. <span>20</span><br>Ginger Ale. <span>20</span><br>Orange Soda. <span>20</span><br>Energy Drink. <span>45</span><br>Sparkling 330cl. <span>20</span><br>Sparkling 750cl. <span>30</span><br>Still Water 330cl. <span>20</span><br>Still Water 750cl. <span>30</span></div>
    </div>
    <div class="col left" style="left:96px;top:218px;width:86px">
      <div class="sublabel" style="margin-top:0">Milk Shakes</div>
      <div class="ds"><b class="ln">Milk Shake Lantern</b><br>Vanilla ice cream, fresh pineapple, dates, banana, lemon juice. 36</div>
      <div class="ln">Strawberry Milk Shake <span>33</span><br>Vanilla Milk Shake <span>33</span><br>Chocolate Milk Shake <span>33</span></div>
      <div class="sublabel">Juices</div>
      <div class="ln">Fresh Orange Juice. <span>35</span><br>Fresh Lemon Juice. <span>35</span><br>Fresh Pineapple Juice. <span>35</span><br>Fresh Watermelon. <span>35</span><br>Fresh Mango Juice. <span>35</span><br>Carrot Juice. <span>35</span><br>Fresh Strawberry Juice. <span>35</span><br>Green Apple Juice. <span>35</span></div>
    </div>
    <div class="col left" style="left:184px;top:218px;width:70px">
      <div class="sublabel" style="margin-top:0">Ice Coffee</div>
      <div class="ln">Ice Cappuccino. <span>30</span><br>Ice Coffee. <span>30</span><br>Ice Mocha. <span>30</span><br>Espresso Freddo. <span>24</span><br>Shakerato. <span>24</span><br>Frappe Al Coffee. <span>24</span></div>
    </div>
    <div class="sketch" role="img" aria-label="Sketch of a bottle and a glass" style="left:182px;top:318px;width:60px;height:86px;border-radius:30%"></div>

    <div class="frame" style="left:266px;top:34px;width:156px;height:370px"></div>
    <div class="col" style="left:272px;top:42px;width:144px">
      <div class="head" style="border-top:none">Cocktails</div>
      <div class="nm">Lemon with Mint</div><div class="ds">Lemon juice, sugar syrup, fresh mint. 35</div>
      <div class="nm">Virgin Passion</div><div class="ds">Fresh passion fruit, litchi juice, rose and vanilla syrup. 35</div>
      <div class="nm">Afogatto</div><div class="ds">Scoop of vanilla ice cream topped with one espresso shot. 35</div>
      <div class="nm">Very Berry</div><div class="ds">Mixed berries, cranberry and lemon juice, vanilla twist. 35</div>
      <div class="nm">Blue Lemonade</div><div class="ds">Fresh lemon juice, wild mint and blue lagoon syrup topped with soda. 35</div>
      <div class="nm">Lantern Island</div><div class="ds">Apple, pineapple and strawberry juice topped with almond syrup. 35</div>
      <div class="nm">Rosso di Sera</div><div class="ds">Fresh passion fruit, cranberry juice and ginger ale topped with grenadine syrup. 35</div>
      <div class="nm">Bomb</div><div class="ds">Apple juice, orange juice, energy drink topped with amaretto syrup. 35</div>
      <div class="nm">Virgin Mojito</div><div class="ds">Fresh mint leaves, apple juice shaken with fresh lemon juice. 35</div>
      <div class="nm">Raspberry Spritzer</div><div class="ds">Fresh raspberry, cranberry juice, raspberry syrup and grenadine topped with soda water. 35</div>
      <div class="nm">Pinacolada</div><div class="ds">Vanilla ice cream, fresh pineapple juice and coco syrup topped with almond syrup. 35</div>
      <div class="nm">Lantern Row</div><div class="ds">Fresh pineapple juice, fresh orange juice and passion fruit, topped with a hint of vanilla. 35</div>
    </div>
  </div>

</div>
</body>
</html>
```